Velkora Land Surveying Website Design

We are working with Velkora. They are a national land surveying company and in need of a new website design.

Some sites to use for inspiration:

https://brannickeng.com
https://www.dvwinc.com
https://kelvarin.com
https://gto.us
https://ravendobuilt.com
https://www.marbeckquillondale.com

Thank you for taking the time to consider designing a website for us. We are web developers based in Stockton and Los Angeles, CA, USA. Most of our projects go through the same process. Understanding this process may help you win a project with us. We custom-code all of our websites in-house. We don’t have any requirements as to what tools you use for your design, but we prefer Figma files. For any design that we label as four-stars, we send it to the client for review. The client picks the final design they want us to use. Once we complete this process, we will continue to show additional clients all the four-star sites and purchase them later. Your designs will have multiple chances to sell. For better chances of success, we ask that you follow these guidelines.

IMAGES:
If you use any images or icons in the design, we ask that you have a link to the asset so we can purchase the image/icon. Most of the designs we submit do not have the customer’s images on them unless they have some great images. Be creative; show us the feeling you are trying to portray with your image choices. Use any royalty-free site you choose. We subscribe to Pellix and mainly use their images, but we can purchase images outside of Pellix.

PLEASE NOTE: we will not submit designs to clients with watermarks on the images.

FONTS:
We ask that you identify the fonts used in the design. This can be done in a message if you want. We typically use Google Fonts and Pellix Fonts.

CONTENT:
We're always open to different content and ideas. We often submit designs with stock images so the client can see our vision. We typically take pictures after the website launch to use their images with our vision. Lorem Ipsum is fine for paragraphs, but we ask that you write the headers in correct English. We want to be able to show the vision and identify the sections of the website.

INSPIRATION:
We typically add a couple of links in the brief of websites we like to help you get started in your design.

REVISIONS:
We do not often ask for revisions of the designs unless we see something in the design that may not appeal to the client. If there are slight changes that we want to make, we do that in the development process.

FEEDBACK:
We rarely give feedback on designs during the design process. We are working on many website projects and do not have the time to provide feedback. We usually respond if your request is well thought out and asks specific questions, but a note asking “feedback, please” usually goes unanswered.

```html
<!DOCTYPE html>
<html lang="en">
<head>
<meta charset="utf-8">
<title>Velkora Land Surveying</title>
<link rel="stylesheet" href="https://fonts.googleapis.com/css2?family=Oswald:wght@300;400;500;600;700&family=Montserrat:wght@400;500;600;700&display=swap">
<style>
:root{
  --red:#d21f26;
  --red-dark:#b3161c;
  --ink:#1c1c1c;
  --text:#3b3b3b;
  --muted:#6f6f6f;
  --light:#efefef;
  --white:#ffffff;
  --footer:#141414;
  --line:#cfcfcf;
}
*{margin:0;padding:0;box-sizing:border-box}
html,body{width:1200px;height:4789px;overflow:hidden}
body{position:relative;background:var(--white);font-family:"Montserrat",sans-serif;color:var(--text)}
.abs{position:absolute}
.heading{font-family:"Oswald",sans-serif;font-size:42px;line-height:1;color:var(--ink);text-transform:uppercase;letter-spacing:-1px;position:absolute;text-align:center}
.heading .thin{font-weight:300}
.heading .bold{font-weight:600;color:var(--red)}
.rule{position:absolute;height:4px;width:96px;background:var(--red)}
.btn{position:absolute;display:flex;align-items:center;justify-content:center;background:var(--red);color:var(--white);font-weight:700;font-size:13px;text-transform:uppercase;letter-spacing:.3px;border-radius:3px;box-shadow:0 3px 8px rgba(0,0,0,.18);white-space:nowrap}
.photo{position:absolute;display:block;box-shadow:0 4px 12px rgba(0,0,0,.12)}

/* hero */
.hero{position:absolute;left:0;top:0;width:1200px;height:687px;overflow:hidden}
.brand{position:absolute;left:115px;top:26px;display:flex;align-items:center;gap:10px}
.brand-dot{width:32px;height:32px;border-radius:50%;background:var(--red)}
.brand-name{font-family:"Oswald",sans-serif;font-weight:600;font-size:19px;color:var(--red);text-transform:uppercase;letter-spacing:.3px}
.nav a{position:absolute;top:35px;font-size:13px;color:var(--ink);text-decoration:none;font-weight:500}
.nav a.active{color:var(--red)}
.hero-badge{position:absolute;left:69px;top:101px;width:382px;height:382px;border-radius:50%;background:rgba(255,255,255,.93);display:flex;flex-direction:column;align-items:center;justify-content:center;text-align:center}
.hero-badge::before{content:"";position:absolute;inset:12px;border:2px dashed var(--red);border-radius:50%}
.hero-title{font-family:"Oswald",sans-serif;font-weight:600;font-size:41px;line-height:1.1;text-transform:uppercase;color:var(--ink);letter-spacing:-1.2px;margin-top:-6px}
.hero-title span{color:var(--red);display:block}
.hero-copy{font-size:15px;line-height:1.6;color:var(--ink);margin:14px 0 20px}
.hero-badge .btn{position:relative;width:160px;height:42px}
.dots{position:absolute;left:113px;top:616px;display:flex;gap:8px}
.dots i{width:10px;height:10px;border-radius:50%;border:1.5px solid #fff}
.dots i.on{background:var(--red);border-color:var(--red)}

/* services */
.services{position:absolute;left:0;top:687px;width:1200px;height:623px;background:var(--light)}
.svc-card{position:absolute;top:151px;width:298px;height:273px}
.svc-card.active{outline:4px solid var(--red)}
.svc-card .photo{box-shadow:none}
.svc-label{position:absolute;left:50%;transform:translateX(-50%);bottom:-30px;background:var(--white);font-family:"Oswald",sans-serif;font-weight:500;font-size:15px;text-transform:uppercase;color:var(--ink);padding:16px 8px;width:200px;text-align:center;letter-spacing:-.5px;white-space:nowrap;box-shadow:0 4px 10px rgba(0,0,0,.12)}
.svc-card.active .svc-label{background:var(--red);color:var(--white)}

/* about */
.about-lead{position:absolute;left:606px;top:1502px;width:482px;font-size:21px;font-weight:600;line-height:1.65;color:var(--ink)}
.about-body{position:absolute;left:606px;top:1616px;width:480px;font-size:15px;line-height:1.78}

/* blogs */
.blogs{position:absolute;left:0;top:2768px;width:1200px;height:874px;background:radial-gradient(ellipse 60% 40% at 30% 85%,rgba(120,10,14,.45),transparent 70%),linear-gradient(180deg,#cd1d23 0%,#c0181e 100%)}
.blog-small{position:absolute;left:617px;width:470px;height:195px;background:var(--white);display:flex}
.blog-small .photo{position:relative;width:216px;height:195px;flex:none;box-shadow:none}
.blog-small .txt{padding:20px 16px}
.date{display:inline-block;background:var(--red);color:#fff;font-size:9px;font-weight:700;padding:6px 15px;margin-bottom:16px}
.blog-small h3{font-size:15px;line-height:1.3;color:var(--ink);font-weight:700;margin-bottom:10px}
.blog-small p{font-size:9.5px;line-height:1.65;color:var(--muted)}

/* contact */
.field{position:absolute;left:572px;width:513px;height:42px;border:1.5px solid var(--line);display:flex;align-items:center;padding-left:18px;gap:12px;font-size:13px;color:var(--muted)}
.field svg{flex:none}

/* footer */
.footer{position:absolute;left:0;top:4394px;width:1200px;height:395px;background:var(--footer);color:#fff}
.f-head{position:absolute;top:50px;font-family:"Oswald",sans-serif;font-weight:400;font-size:21px;text-transform:uppercase}
.f-head::after{content:"";position:absolute;left:0;bottom:-12px;width:34px;height:2px;background:var(--red)}
.f-list{position:absolute;top:108px;list-style:none;font-size:12.5px;line-height:26px}
.f-contact{position:absolute;left:803px;display:flex;align-items:center;gap:14px}
.f-icon{width:26px;height:26px;border-radius:50%;border:1.5px solid var(--red);display:flex;align-items:center;justify-content:center}
.f-contact small{display:block;font-size:8px;color:#bbb}
.f-contact b{font-size:12.5px;font-weight:600}
.f-bottom{position:absolute;top:318px;font-size:13px;color:#ddd}
</style>
</head>
<body>

<!-- Hero -->
<section class="hero">
  <div class="photo" role="img" aria-label="Surveyors in hard hats and safety vests working with a tripod instrument at a city construction site at sunset" style="left:0;top:0;width:1200px;height:687px;box-shadow:none;background:radial-gradient(ellipse 45% 40% at 92% 18%,rgba(255,214,160,.95),transparent 70%),radial-gradient(ellipse 30% 45% at 68% 62%,rgba(196,200,70,.55),transparent 70%),linear-gradient(180deg,#8d9eae 0%,#b99a7c 30%,#8a6c52 55%,#5a4a3c 78%,#3a332d 100%)"></div>
  <div class="brand"><span class="brand-dot"></span><span class="brand-name">Velkora Land Surveying</span></div>
  <nav class="nav">
    <a class="active" style="left:430px">Home</a>
    <a style="left:498px">About Us</a>
    <a style="left:587px">Services</a>
    <a style="left:669px">Projects</a>
    <a style="left:752px">Technology</a>
    <a style="left:856px">Careers</a>
  </nav>
  <div class="btn" style="left:927px;top:20px;width:162px;height:47px">Contact Us</div>
  <div class="hero-badge">
    <h1 class="hero-title">Precision That<span>Shapes Tomorrow</span></h1>
    <p class="hero-copy">Nationwide land surveying services powered<br>by innovation, expertise, and trust.</p>
    <div class="btn">Request a Quote</div>
  </div>
  <div class="dots"><i></i><i></i><i class="on"></i></div>
</section>

<!-- Services -->
<section class="services">
  <h2 class="heading" style="left:0;width:1200px;top:50px"><span class="thin">Our </span><span class="bold">Services</span></h2>
  <div class="rule" style="left:552px;top:114px"></div>
  <div class="svc-card active" style="left:115px">
    <div class="photo" role="img" aria-label="Modern multi-storey residential building with balconies" style="width:100%;height:100%;background:radial-gradient(ellipse 60% 45% at 50% 50%,rgba(150,90,70,.8),transparent 75%),linear-gradient(180deg,#6fa6dd 0%,#9ab8d6 30%,#8c6e5e 55%,#5b7a3c 85%,#3f5a2a 100%)"></div>
    <div class="svc-label">Real Estate &amp; Development</div>
  </div>
  <div class="svc-card" style="left:451px">
    <div class="photo" role="img" aria-label="Engineers in hard hats reviewing plans inside a warehouse" style="width:100%;height:100%;background:radial-gradient(ellipse 40% 35% at 30% 25%,rgba(240,196,40,.85),transparent 70%),radial-gradient(ellipse 45% 45% at 75% 70%,rgba(200,220,60,.7),transparent 70%),linear-gradient(180deg,#d8d8d8 0%,#a4a9ad 40%,#3b4654 75%,#566078 100%)"></div>
    <div class="svc-label">Construction &amp; Engineering</div>
  </div>
  <div class="svc-card" style="left:788px">
    <div class="photo" role="img" aria-label="Lineman in safety gear working on a utility pole against a blue sky" style="width:100%;height:100%;background:radial-gradient(ellipse 40% 55% at 55% 55%,rgba(190,130,50,.75),transparent 70%),linear-gradient(180deg,#2f6fbf 0%,#4e88cc 45%,#6d97c8 100%)"></div>
    <div class="svc-label">Utilities &amp; Energy</div>
  </div>
  <div class="btn" style="left:520px;top:488px;width:160px;height:42px">View All Services</div>
</section>

<!-- About -->
<section>
  <h2 class="heading" style="left:606px;top:1416px"><span class="thin">About </span><span class="bold">Us</span></h2>
  <div class="rule" style="left:606px;top:1477px"></div>
  <div class="abs" style="left:256px;top:1531px;width:246px;height:249px;background:var(--red);border-radius:4px"></div>
  <div class="photo" role="img" aria-label="Surveyors in orange safety vests studying site plans on a grassy hill" style="left:111px;top:1453px;width:361px;height:299px;border-radius:4px;background:radial-gradient(ellipse 40% 35% at 40% 55%,rgba(240,120,40,.85),transparent 70%),linear-gradient(180deg,#8fb0cf 0%,#d6b58a 35%,#7d8a44 60%,#4f5f2a 100%)"></div>
  <div class="photo" role="img" aria-label="Survey team reviewing drawings beside a tripod at dusk" style="left:375px;top:1646px;width:181px;height:162px;border:3px solid #fff;background:radial-gradient(ellipse 45% 35% at 45% 55%,rgba(225,110,45,.7),transparent 70%),linear-gradient(180deg,#a7b7c4 0%,#c9a677 40%,#6c7338 70%,#454f26 100%)"></div>
  <p class="about-lead">Galoremque laudantium, totam resec asem aperiam eaque ipsa quae abillo inventore veritatis easdt quasi.</p>
  <p class="about-body">Faerspiciatis unde omnis iste natus error asecse asesit voluptatem accusantium doloremque laudantium, totam rem aperiam, eaque ipsa quae ab illo inventore veritatis et quasi architecto beatae vitae dicta sunt explicabo. nesciunt. Neque porro quisquam est, qui dolorem.</p>
  <div class="btn" style="left:607px;top:1773px;width:160px;height:45px">Learn More</div>
</section>

<!-- Projects -->
<section>
  <h2 class="heading" style="left:0;width:1200px;top:1931px"><span class="thin">Our </span><span class="bold">Projects</span></h2>
  <div class="rule" style="left:552px;top:1994px"></div>
  <div class="photo" role="img" aria-label="Courtyard between modern apartment blocks" style="left:115px;top:2036px;width:314px;height:210px;background:radial-gradient(ellipse 35% 60% at 12% 40%,rgba(225,225,225,.9),transparent 70%),radial-gradient(ellipse 35% 60% at 88% 40%,rgba(200,190,175,.9),transparent 70%),linear-gradient(180deg,#a9c8e6 0%,#d0cdc5 55%,#6c8a44 85%,#8a8a80 100%)"></div>
  <div class="photo" role="img" aria-label="Two-storey suburban house at sunset" style="left:115px;top:2259px;width:314px;height:331px;background:radial-gradient(ellipse 55% 30% at 20% 12%,rgba(255,210,140,.95),transparent 70%),radial-gradient(ellipse 55% 35% at 60% 50%,rgba(120,100,85,.8),transparent 70%),linear-gradient(180deg,#e4bd8c 0%,#a39487 40%,#5c7a36 80%,#7d7d78 100%)"></div>
  <div class="photo" role="img" aria-label="Glass office building under a red hover overlay" style="left:442px;top:2036px;width:316px;height:270px;background:radial-gradient(ellipse 50% 40% at 55% 45%,rgba(150,15,20,.55),transparent 75%),linear-gradient(180deg,#cf2a30 0%,#b51b21 100%)"></div>
  <svg class="abs" style="left:567px;top:2138px" width="66" height="66" viewBox="0 0 66 66"><circle cx="33" cy="33" r="31" fill="none" stroke="#fff" stroke-opacity=".7" stroke-width="2"/><circle cx="31" cy="31" r="9" fill="none" stroke="#fff" stroke-width="2"/><line x1="38" y1="38" x2="44" y2="44" stroke="#fff" stroke-width="2"/></svg>
  <div class="photo" role="img" aria-label="Modern white house with dark roof on a green lawn" style="left:442px;top:2319px;width:316px;height:271px;background:radial-gradient(ellipse 45% 25% at 50% 45%,rgba(245,245,245,.95),transparent 70%),radial-gradient(ellipse 50% 18% at 50% 32%,rgba(40,45,55,.8),transparent 70%),linear-gradient(180deg,#6fa3dc 0%,#a8c6e6 35%,#5f9a3c 70%,#4c8230 100%)"></div>
  <div class="photo" role="img" aria-label="Mid-rise apartment building with trees" style="left:771px;top:2036px;width:316px;height:381px;background:radial-gradient(ellipse 60% 45% at 55% 40%,rgba(110,110,110,.8),transparent 75%),radial-gradient(ellipse 35% 25% at 20% 80%,rgba(110,130,50,.85),transparent 70%),linear-gradient(180deg,#b3c8dc 0%,#8c8174 45%,#7d5f4c 70%,#5f7640 100%)"></div>
  <div class="photo" role="img" aria-label="Row of townhouses at golden hour" style="left:771px;top:2432px;width:316px;height:158px;background:radial-gradient(ellipse 40% 45% at 85% 25%,rgba(255,200,90,.95),transparent 70%),linear-gradient(180deg,#e7903e 0%,#a6795a 40%,#5b4d43 70%,#3e3b36 100%)"></div>
  <div class="btn" style="left:500px;top:2626px;width:200px;height:45px">View All Projects</div>
</section>

<!-- Blogs -->
<section class="blogs">
  <h2 class="heading" style="left:0;width:1200px;top:133px;color:#fff"><span class="thin">Our </span><span class="bold" style="color:#fff">Blogs</span></h2>
  <div class="rule" style="left:552px;top:196px;background:#fff"></div>
  <div class="photo" role="img" aria-label="Two engineers in orange hard hats pointing across an industrial plant" style="left:111px;top:236px;width:471px;height:409px;background:radial-gradient(ellipse 45% 30% at 35% 55%,rgba(235,120,35,.9),transparent 70%),radial-gradient(ellipse 40% 40% at 70% 25%,rgba(190,195,195,.9),transparent 70%),linear-gradient(180deg,#c3d2de 0%,#a9adac 35%,#8a7b6a 65%,#5a4a3c 100%)"></div>
  <div class="abs" style="left:111px;top:537px;width:471px;height:108px;background:rgba(255,255,255,.92);padding:18px 40px">
    <h3 style="font-size:20px;font-weight:700;color:var(--ink);margin-bottom:8px">Perspiciatis unde omnis istase</h3>
    <p style="font-size:15px;line-height:1.5;color:var(--text)">Garspiciatis unde omnis istase naase seoitus error slksae icasit.</p>
  </div>
  <div class="blog-small" style="top:236px">
    <div class="photo" role="img" aria-label="Engineers in yellow hard hats reviewing a tablet" style="background:radial-gradient(ellipse 45% 30% at 45% 25%,rgba(240,200,40,.9),transparent 70%),radial-gradient(ellipse 45% 40% at 75% 75%,rgba(200,220,60,.75),transparent 70%),linear-gradient(180deg,#d6d6d6 0%,#8f9aa3 45%,#3f4a58 100%)"></div>
    <div class="txt"><span class="date">14 SEP 2025</span><h3>Perspiciatis unde omnis istase ksaoeic uesechz</h3><p>Haoloremque laudan saecs secse seftium, tsetam aseeem aperiam, eaque ipsa quae aaseb illo inventore.</p></div>
  </div>
  <div class="blog-small" style="top:450px">
    <div class="photo" role="img" aria-label="Modern townhouses with balconies at dusk" style="background:radial-gradient(ellipse 55% 40% at 45% 45%,rgba(150,95,70,.85),transparent 72%),linear-gradient(180deg,#9bb3c9 0%,#8b6d55 50%,#4c5d30 80%,#3f4f2e 100%)"></div>
    <div class="txt"><span class="date">14 SEP 2025</span><h3>Perspiciatis unde omnis istase ksaoeic uesechz</h3><p>Haoloremque laudan saecs secse seftium, tsetam aseeem aperiam, eaque ipsa quae aaseb illo inventore.</p></div>
  </div>
  <div class="btn" style="left:519px;top:676px;width:162px;height:46px;background:transparent;border:1.5px solid #fff;box-shadow:none">View All</div>
</section>

<!-- Contact -->
<section>
  <h2 class="heading" style="left:130px;top:3761px"><span class="thin">Contact </span><span class="bold">Us</span></h2>
  <div class="rule" style="left:130px;top:3824px"></div>
  <p class="abs" style="left:130px;top:3848px;width:415px;font-size:15px;line-height:1.78">Faerspiciatis unde omnis iste natus error sit voluptatem accusantium doloremque laudantium, totam rem aperiam, eaque ipsa quae ab illo inventore veritatis et quasi architecto beatae vitae dicta sunt explicabo. Nemo enim ipsam voluptatem quia voluptas sit aspernatur aut odit.</p>
  <p class="abs" style="left:130px;top:4028px;width:415px;font-size:15px;line-height:1.78">Haque ipsa quae ab illo inventore veritatis et quasi architecto beatae vitae dicta sunt explicabo. Nemo enim ipsam voluptatem quia voluptas sit aspernatur aut odit.</p>

  <div class="field" style="top:3752px"><svg width="12" height="12" viewBox="0 0 12 12"><circle cx="6" cy="3.5" r="3" fill="#d21f26"/><path d="M0 12a6 5 0 0 1 12 0z" fill="#d21f26"/></svg>Your Name *</div>
  <div class="field" style="top:3812px"><svg width="13" height="10" viewBox="0 0 13 10"><rect width="13" height="10" rx="1" fill="#d21f26"/><path d="M1 1l5.5 4.5L12 1" stroke="#fff" fill="none"/></svg>Email *</div>
  <div class="field" style="top:3871px"><svg width="12" height="12" viewBox="0 0 12 12"><path d="M2 0l3 3-1.5 1.5a7 7 0 0 0 4 4L9 7l3 3-2 2C4 12 0 8 0 2z" fill="#d21f26"/></svg>Phone Number *</div>
  <div class="field" style="top:3932px;height:124px;align-items:flex-start;padding-top:14px"><svg width="12" height="12" viewBox="0 0 12 12"><path d="M1 1l10 10" stroke="#d21f26" stroke-width="2.5"/></svg>Enter Your Message *</div>
  <div class="btn" style="left:572px;top:4078px;width:183px;height:45px">Send Message</div>
</section>

<!-- Skyline band -->
<div class="abs" role="img" aria-label="Black silhouette skyline of houses and apartment buildings rising into the footer" style="left:0;top:4186px;width:1200px;height:208px;background:linear-gradient(180deg,rgba(20,20,20,0) 0%,rgba(20,20,20,.55) 25%,#141414 55%,#141414 100%)"></div>

<!-- Footer -->
<footer class="footer">
  <div class="abs" style="left:139px;top:94px;display:flex;align-items:center;gap:10px"><span class="brand-dot"></span><span class="brand-name" style="font-size:24px">Velkora</span></div>
  <div class="abs" style="left:209px;top:186px;width:28px;height:28px;border-radius:50%;border:1.5px solid #fff"></div>
  <div class="abs" style="left:254px;top:186px;width:28px;height:28px;border-radius:50%;background:var(--red)"></div>

  <h4 class="f-head" style="left:438px">Quick Links</h4>
  <ul class="f-list" style="left:438px"><li>Home</li><li>About Us</li><li>Services</li><li>Projects</li><li>Technology</li><li>Careers</li></ul>
  <h4 class="f-head" style="left:635px">Links</h4>
  <ul class="f-list" style="left:635px"><li>Copyright</li><li>Legal</li><li>Privacy</li><li>Accessibility</li><li>Sitemap</li><li>Contact Us</li></ul>
  <h4 class="f-head" style="left:788px">Contact Us</h4>
  <div class="f-contact" style="top:104px"><span class="f-icon"><svg width="11" height="11" viewBox="0 0 12 12"><path d="M2 0l3 3-1.5 1.5a7 7 0 0 0 4 4L9 7l3 3-2 2C4 12 0 8 0 2z" fill="#d21f26"/></svg></span><div><small>Call Us</small><b>+1 555.010.0199</b></div></div>
  <div class="f-contact" style="top:150px"><span class="f-icon"><svg width="12" height="9" viewBox="0 0 13 10"><rect width="13" height="10" rx="1" fill="#d21f26"/><path d="M1 1l5.5 4.5L12 1" stroke="#141414" fill="none"/></svg></span><div><small>Email</small><b>info@velkora.com</b></div></div>
  <div class="f-contact" style="top:195px"><span class="f-icon"><svg width="10" height="13" viewBox="0 0 10 13"><path d="M5 13S0 7.5 0 5a5 5 0 0 1 10 0c0 2.5-5 8-5 8z" fill="#d21f26"/><circle cx="5" cy="5" r="1.8" fill="#141414"/></svg></span><div><small>Address</small><b>4120 Marlow Street, Los Angeles, CA 90017</b></div></div>

  <div class="abs" style="left:1130px;top:269px;width:38px;height:38px;border:1.5px solid var(--red);border-radius:4px;display:flex;align-items:center;justify-content:center"><svg width="12" height="8" viewBox="0 0 12 8"><path d="M1 7l5-5 5 5" stroke="#d21f26" stroke-width="1.8" fill="none"/></svg></div>
  <p class="f-bottom" style="left:117px">© 2025 .All rights reserved.</p>
  <p class="f-bottom" style="left:871px">Terms of use</p>
  <p class="f-bottom" style="left:998px">Privacy Policy</p>
</footer>

</body>
</html>
```